Bicycle dealer and service & repair center

The registered brand of our company, Rad Lindhof, means bicycle of the city Zurich (Switzerland) and is the largest dealer of e-bikes, folding bikes and cargo bikes in Switzerland. Rad Lindhof also sells a substantial amount of road bikes, mountainbikes, trailers and bicycles without electric motor. The more, we are known for special bikes (tandems, Swiss military bicycles, postman bicycles, and others).Rad Lindhof has around 10 highly skilled employees and runs a well-equipped service & repair center. We have around 50 brand dealerships for replacement parts, diagnostic devices and are proud about our after-sales service.Our website is fully functional (see www.rad-lindhof.ch) and available in three languages (DE, EN, FR for the french speaking part of Switzerland). Live stock information is provided by https://www.rad-lindhof.ch/en/rad.We need a redesign of our website. The focus should be on:- e-catalog with simple search and extended search - e-commerce (e.g. add to chart, favorites, text search, filter, sort, related products, similar products, most popular search, related articles, top listings, promotions...)- cross-selling with our affiliated company Rad Brunnegg, our bicycle shop in a city nearby Zurich.- service and repair- company (sustainable business, emission-free mobility, public relation, well-trained and friendly staff)- mobile friendlyness- maximize usability- maximize usage of display for useful information- easy to find relevant information- simple search functionalityKey audience is:- middle to high-price bicycle customers- existing and returning clients- prospective employees- members of the pressThe goal of the website and its redesign is:- increase the number of enquiries via website- increase online sales- share information with others (addtoany)- provide information about the right selection of bicycle (faq, detailed information about components) to reduce the admin associated with new enquiries- highlight special offers (e.g. free bicycle service slots, sunday exhibition)As Rad Lindhof has many returning customers and already high website traffic (according to SERP), the new design should be a smooth transition from the existing website.Websites we like:- https://tramofix.ch/- https://www.kurbelhaus.ch/- https://www.quandor.ch/- https://www.autoscout24.ch/deGood luck and have fun creating our new design!
Updates

website we also like: https://www.pedalora.ch/

Target Market(s)

Urban bicycle riders

Industry/Entity Type

Retail

Coding

Coded - Design and coding required

Number of Pages Required

5+ page

Font styles to use
Other font styles liked:
• Avenir (https://www.glyphbazar.com/fonts/typecraft/avenir/)

Colors

Designer to choose colors to be used in the design.

Requirements
Must have
• The actual content www.rad-lindhof.ch must be published with the new website design. Additional content should be added according to project description (see above).
Nice to have
• - we use the font type Avenir (https://www.glyphbazar.com/fonts/typecraft/avenir/) for business cards, leaflets etc
Should not have
• Frippery

```html
<!DOCTYPE html>
<html lang="en">
<head>
<meta charset="utf-8">
<title>Rad Lindhof – E-Bikes, Folding Bikes, Cargo Bikes</title>
<link rel="stylesheet" href="https://fonts.googleapis.com/css2?family=Nunito+Sans:wght@400;600;700;800&display=swap">
<style>
:root{
  --blue:#1a64a8;
  --blue-dark:#124d84;
  --ink:#1f2328;
  --text:#4a4f55;
  --muted:#8a9097;
  --line:#e1e3e6;
  --panel:#f0f0f1;
  --tile:#ececed;
  --white:#ffffff;
  --footer:#2b2d30;
  --footer-deep:#222326;
  --red:#c8102e;
}
*{box-sizing:border-box;margin:0;padding:0}
html,body{width:1200px;height:4928px;overflow:hidden}
body{font-family:"Nunito Sans",Arial,sans-serif;color:var(--text);background:var(--white);font-size:13px;position:relative}
a{color:inherit;text-decoration:none}
.wrap{width:960px;margin:0 auto;position:relative}
.btn{display:inline-block;background:var(--blue);color:var(--white);font-weight:700;font-size:11px;letter-spacing:.5px;padding:7px 12px;border-radius:2px}
.btn-outline{display:inline-block;border:1px solid var(--blue);color:var(--blue);font-weight:700;font-size:11px;letter-spacing:.5px;padding:8px 14px;border-radius:2px;background:var(--white)}
.ph{display:block}

/* header */
.site-header{height:120px;border-bottom:1px solid var(--line)}
.brand{position:absolute;left:0;top:18px;display:flex;align-items:center;gap:10px}
.brand-name{font-size:30px;font-weight:800;color:var(--ink);letter-spacing:.5px;line-height:1}
.brand-square{width:34px;height:34px;background:var(--blue);border-radius:3px}
.brand-tag{position:absolute;left:0;top:58px;font-size:10px;color:var(--muted)}
.search{position:absolute;left:376px;top:16px;width:290px;height:34px;border:1px solid var(--line);display:flex}
.search span{flex:1;font-size:11px;font-weight:700;color:var(--muted);padding:10px 12px}
.search i{width:34px;background:var(--blue);display:flex;align-items:center;justify-content:center}
.fav{position:absolute;left:690px;top:16px;height:34px;border:1px solid var(--line);padding:0 14px;display:flex;align-items:center;gap:6px;font-size:11px;font-weight:700;color:var(--ink)}
.cart{position:absolute;left:820px;top:16px;height:34px;border:1px solid var(--line);padding:0 14px;display:flex;align-items:center;gap:6px;font-size:11px;font-weight:700;color:var(--ink)}
.main-nav{position:absolute;left:376px;top:78px;display:flex;gap:26px;font-size:12px;font-weight:700;color:var(--ink)}
.main-nav a.active{color:var(--blue);border-bottom:2px solid var(--blue);padding-bottom:6px}

/* hero */
.hero{height:540px;position:relative;background:linear-gradient(180deg,#7fb2de 0%,#a9cbe6 45%,#6d7f93 70%,#3d4654 100%)}
.hero .wrap{padding-top:140px}
.hero h1{font-size:44px;font-weight:800;color:var(--ink);letter-spacing:.5px}
.hero p{font-size:18px;color:var(--ink);width:420px;margin:10px 0 24px;line-height:1.4}
.hero .btn{font-size:14px;padding:12px 22px}
.dots{position:absolute;left:50%;bottom:26px;transform:translateX(-50%);display:flex;gap:8px}
.dots b{width:9px;height:9px;border-radius:50%;background:rgba(255,255,255,.55)}
.dots b.on{background:var(--white)}

/* categories */
.categories{display:flex;gap:12px;padding:30px 8px 0}
.cat{flex:1;height:300px;background:var(--tile);position:relative}
.cat .ph{position:absolute;right:14px;top:24px;width:250px;height:240px;border-radius:4px;background:linear-gradient(135deg,#d8dadc,#b9bdc1)}
.cat h3{position:absolute;left:18px;bottom:62px;font-size:26px;font-weight:800;color:var(--ink);line-height:1;z-index:1}
.cat .btn{position:absolute;left:18px;bottom:22px}

/* catalog */
.catalog{padding-top:60px;height:1310px}
.filters{position:absolute;left:0;top:0;width:228px}
.filters h4{font-size:11px;font-weight:800;color:var(--ink);margin-bottom:14px;letter-spacing:.5px}
.filter{background:var(--panel);border-bottom:1px solid var(--white);padding:12px 14px;font-size:11px;font-weight:800;color:var(--ink);display:flex;justify-content:space-between}
.filter-open{background:var(--panel);padding:4px 14px 14px;border-bottom:1px solid var(--white)}
.filter-open li{list-style:none;font-size:11px;color:var(--text);padding:5px 0 5px 8px;border-bottom:1px solid var(--line)}
.products{position:absolute;left:244px;top:0;width:716px}
.section-head{display:flex;justify-content:space-between;align-items:center;margin-bottom:22px}
.section-head h2{font-size:28px;font-weight:800;color:var(--ink)}
.sort{font-size:10px;font-weight:700;color:var(--ink);display:flex;align-items:center;gap:8px}
.sort span{border:1px solid var(--line);padding:5px 24px 5px 8px}
.grid{display:grid;grid-template-columns:repeat(3,1fr);gap:12px}
.card{border:1px solid var(--line);height:262px;text-align:center;padding:16px 12px 0;background:var(--white)}
.card .ph{height:160px;border-radius:3px;background:linear-gradient(135deg,#f4f5f6,#d9dcdf)}
.card h5{font-size:13px;font-weight:700;color:var(--ink);margin-top:16px;white-space:nowrap;overflow:hidden}
.card .price{font-size:18px;font-weight:800;color:var(--blue);margin-top:4px}
.pager{position:absolute;right:0;top:1138px;display:flex;gap:6px}
.pager b{width:22px;height:22px;border:1px solid var(--line);border-radius:50%;font-size:10px;display:flex;align-items:center;justify-content:center;color:var(--muted)}
.pager b.cur{background:var(--ink);color:var(--white);border-radius:3px;width:30px}
.pager b.next{background:var(--red);border-color:var(--red);color:var(--white);border-radius:3px;width:30px}

/* listings */
.band{background:var(--panel)}
.listings{height:560px;padding-top:50px}
.band-head{display:flex;justify-content:space-between;align-items:center;margin-bottom:26px}
.band-head h2{font-size:30px;font-weight:800;color:var(--ink)}
.row4{display:grid;grid-template-columns:repeat(4,1fr);gap:16px}
.lcard{background:var(--white);height:400px;padding:14px}
.lcard .ph{height:130px;border-radius:3px;background:linear-gradient(135deg,#f4f5f6,#d6d9dc)}
.lcard h5{font-size:15px;font-weight:700;color:var(--ink);margin-top:14px}
.lcard .price{font-size:18px;font-weight:800;color:var(--blue);margin:4px 0 14px}
.lcard ul{list-style:none;font-size:10.5px;line-height:1.7;color:var(--text);margin-bottom:14px}

/* articles */
.articles{height:560px;padding-top:60px}
.row3{display:grid;grid-template-columns:repeat(3,1fr);gap:28px}
.acard .ph{height:200px;border-radius:2px}
.acard h4{font-size:19px;font-weight:800;color:var(--ink);line-height:1.3;margin:22px 0 10px;padding-right:20px}
.acard p{font-size:13px;line-height:1.5;margin-bottom:18px;padding-right:30px}

/* promotion */
.promo{height:500px;padding-top:50px}
.row2{display:grid;grid-template-columns:repeat(2,1fr);gap:28px}
.pcard{background:var(--white);height:340px;position:relative;padding:28px 26px}
.pcard h3{font-size:30px;font-weight:700;color:var(--ink)}
.pcard .price{font-size:22px;font-weight:800;color:var(--blue);margin-top:8px}
.pcard .old{font-size:16px;color:var(--muted);text-decoration:line-through}
.pcard .off{display:inline-block;background:var(--blue);color:var(--white);font-size:14px;font-weight:700;padding:8px 14px;margin:20px 0}
.pcard .btn-outline{display:block;width:max-content}
.pcard .ph{position:absolute;right:20px;top:60px;width:260px;height:230px;border-radius:3px;background:linear-gradient(135deg,#f3f3f4,#d5d8db)}

/* similar */
.similar{height:540px;padding-top:40px}
.arrows{display:flex;gap:10px;color:var(--muted);font-size:20px}

/* footer */
.site-footer{background:var(--footer);height:300px;color:#c7c9cc;padding-top:40px}
.f-logo{position:absolute;left:0;top:0;width:150px;height:150px;background:var(--blue);border-radius:4px;display:flex;align-items:center;justify-content:center;color:var(--white);font-weight:800;font-size:16px;letter-spacing:.5px}
.fcol{position:absolute;top:0;font-size:11px;line-height:1.9}
.fcol h6{font-size:11px;font-weight:800;color:var(--white);letter-spacing:.5px;margin-bottom:8px}
.fline{display:flex;align-items:center;gap:8px;margin-bottom:8px}
.social{display:flex;align-items:center;gap:8px;margin-bottom:10px}
.social b{width:22px;height:22px;border-radius:50%;background:var(--blue)}
.copy{background:var(--footer-deep);height:48px;color:#8b8e92;font-size:11px;text-align:center;line-height:48px}
</style>
</head>
<body>

<header class="site-header">
  <div class="wrap" style="height:120px">
    <a class="brand" href="#"><span class="brand-square"></span><span class="brand-name">RAD LINDHOF</span></a>
    <div class="brand-tag">E-Bikes, Cargo Bikes, Folding Bikes · Service &amp; Repair</div>
    <div class="search"><span>SEARCH PRODUCTS</span><i><svg width="14" height="14" viewBox="0 0 14 14"><circle cx="6" cy="6" r="4.3" fill="none" stroke="#fff" stroke-width="1.6"/><line x1="9.2" y1="9.2" x2="13" y2="13" stroke="#fff" stroke-width="1.8"/></svg></i></div>
    <a class="fav" href="#"><svg width="14" height="12" viewBox="0 0 14 12"><path d="M7 11.5 1.5 6A3 3 0 0 1 7 2a3 3 0 0 1 5.5 4Z" fill="none" stroke="#1a64a8" stroke-width="1.4"/></svg>FAVORITES</a>
    <a class="cart" href="#"><svg width="14" height="13" viewBox="0 0 14 13"><path d="M1 1h2l2 8h7l1.5-6H4" fill="none" stroke="#1a64a8" stroke-width="1.4"/><circle cx="6" cy="11.5" r="1" fill="#1a64a8"/><circle cx="11" cy="11.5" r="1" fill="#1a64a8"/></svg>CART</a>
    <nav class="main-nav"><a class="active" href="#">HOME</a><a href="#">VELOS</a><a href="#">NEWS</a><a href="#">SERVICES</a><a href="#">ABOUT US</a><a href="#">FAQ</a><a href="#">CONTACT US</a></nav>
  </div>
</header>

<section class="hero" role="img" aria-label="Mountain biker jumping over a rocky ridge under a blue sky">
  <div class="wrap">
    <h1>MOUNTAIN BIKES</h1>
    <p>With 1080 vehicles, Switzerland's largest selection of e-bikes, transport bikes and folding bikes.</p>
    <a class="btn" href="#">SHOP NOW</a>
  </div>
  <div class="dots"><b></b><b class="on"></b><b></b><b></b><b></b></div>
</section>

<section class="categories">
  <div class="cat"><span class="ph" role="img" aria-label="Green folding bike"></span><h3>FOLDING<br>BIKE</h3><a class="btn" href="#">SHOP NOW</a></div>
  <div class="cat"><span class="ph" role="img" aria-label="Dark green e-bike"></span><h3>E-BIKE</h3><a class="btn" href="#">SHOP NOW</a></div>
  <div class="cat"><span class="ph" role="img" aria-label="Black cargo bike"></span><h3>CARGO BIKE</h3><a class="btn" href="#">SHOP NOW</a></div>
</section>

<section class="catalog">
  <div class="wrap">
    <aside class="filters">
      <h4>FILTER BY</h4>
      <div class="filter">POWER<span>+</span></div>
      <div class="filter">TYPE<span>–</span></div>
      <ul class="filter-open">
        <li>City / Trekking bike (436)</li><li>Folding bike (273)</li><li>Transport wheel 2-wheel (77)</li><li>Transport wheel 3-wheel (8)</li><li>Military bike (13)</li><li>Tandem (9)</li><li>Mountain bike (44)</li><li>Racing bike (47)</li><li>Velo Trailer (56)</li>
      </ul>
      <div class="filter">BRAND<span>+</span></div>
      <div class="filter">PRICE<span>+</span></div>
      <div class="filter">STATE<span>+</span></div>
      <div class="filter">PROMOTION<span>+</span></div>
      <div class="filter">FRAME<span>+</span></div>
      <div class="filter">HEIGHT<span>+</span></div>
      <div class="filter">ENGINE<span>+</span></div>
      <div class="filter">DRIVE<span>+</span></div>
      <div class="filter">AVAILABILITY<span>+</span></div>
      <div class="filter">LOCATION<span>+</span></div>
      <div class="filter">COLOUR<span>+</span></div>
    </aside>
    <div class="products">
      <div class="section-head"><h2>OUR PRODUCTS</h2><div class="sort">SORT BY <span>NEWEST</span></div></div>
      <div class="grid">
        <div class="card"><span class="ph" role="img" aria-label="Red e-bike"></span><h5>Ridgeway R7</h5><div class="price">CHF 3,949</div></div>
        <div class="card"><span class="ph" role="img" aria-label="Teal city bike"></span><h5>Stadtfluss E</h5><div class="price">CHF 2,999.-</div></div>
        <div class="card"><span class="ph" role="img" aria-label="Green cargo bike"></span><h5>Lastkahn L6 Cargo</h5><div class="price">CHF 5'150.-</div></div>
        <div class="card"><span class="ph" role="img" aria-label="Black trekking bike"></span><h5>Talweg Trekking 6</h5><div class="price">CHF 2'599.-</div></div>
        <div class="card"><span class="ph" role="img" aria-label="Dark e-bike"></span><h5>Föhnwind Light</h5><div class="price">CHF 3,998.-</div></div>
        <div class="card"><span class="ph" role="img" aria-label="Red folding bike"></span><h5>Faltgut F3</h5><div class="price">CHF 1'850</div></div>
        <div class="card"><span class="ph" role="img" aria-label="Red e-bike"></span><h5>Ridgeway R7</h5><div class="price">CHF 3,949</div></div>
        <div class="card"><span class="ph" role="img" aria-label="Teal e-bike"></span><h5>Ridgeway R7</h5><div class="price">CHF 3'899.-</div></div>
        <div class="card"><span class="ph" role="img" aria-label="Red city bike"></span><h5>Limmat i7</h5><div class="price">CHF 1,280.-</div></div>
        <div class="card"><span class="ph" role="img" aria-label="Brown cruiser bike"></span><h5>Seeufer Cruiser</h5><div class="price">Fr. 4'138</div></div>
        <div class="card"><span class="ph" role="img" aria-label="Green child trailer"></span><h5>Kinderzug 1</h5><div class="price">CHF 1,479.-</div></div>
        <div class="card"><span class="ph" role="img" aria-label="Red city bike"></span><h5>Limmat i7</h5><div class="price">CHF 1,280.-</div></div>
      </div>
    </div>
    <div class="pager"><b>‹</b><b class="cur">1</b><b>2</b><b>3</b><b>4</b><b>…</b><b>23</b><b class="next">›</b></div>
  </div>
</section>

<section class="band listings">
  <div class="wrap">
    <div class="band-head"><h2>TOP LISTINGS</h2><a class="btn-outline" href="#">VIEW ALL LISTINGS</a></div>
    <div class="row4">
      <div class="lcard"><span class="ph" role="img" aria-label="Blue bike trailer"></span><h5>Kinderzug 2</h5><div class="price">CHF 1'599.-</div><ul><li>Performance : bike without engine</li><li>Type : bike trailer</li><li>Circuit : no</li><li>Size : universal</li><li>Vehicle ID : 272956</li></ul><a class="btn" href="#">ADD TO CART</a></div>
      <div class="lcard"><span class="ph" role="img" aria-label="Red city bike"></span><h5>Quartier 4</h5><div class="price">CHF 4'079.-</div><ul><li>Performance : bike without engine</li><li>Type : bike trailer</li><li>Circuit : no</li><li>Size : universal</li><li>Vehicle ID : 272956</li></ul><a class="btn" href="#">ADD TO CART</a></div>
      <div class="lcard"><span class="ph" role="img" aria-label="Black e-bike"></span><h5>Hangar GH 5</h5><div class="price">CHF 5'259.-</div><ul><li>Performance : bike without engine</li><li>Type : bike trailer</li><li>Circuit : no</li><li>Size : universal</li><li>Vehicle ID : 272956</li></ul><a class="btn" href="#">ADD TO CART</a></div>
      <div class="lcard"><span class="ph" role="img" aria-label="Green child trailer"></span><h5>Anhänger Duo</h5><div class="price">1'199.-</div><ul><li>Performance : bike without engine</li><li>Type : bike trailer</li><li>Circuit : no</li><li>Size : universal</li><li>Vehicle ID : 272956</li></ul><a class="btn" href="#">ADD TO CART</a></div>
    </div>
  </div>
</section>

<section class="articles">
  <div class="wrap">
    <div class="band-head"><h2>ARTICLES</h2><a class="btn-outline" href="#">VIEW ALL ARTICLES</a></div>
    <div class="row3">
      <div class="acard"><span class="ph" role="img" aria-label="Rider on a mountain trail" style="background:linear-gradient(180deg,#8fb6da,#6f8aa4 55%,#4a5a48)"></span><h4>Lorem Ipsum is simply dumt ext of the printing</h4><p>There are many variations of pass ages of Lorem Ipsum available but the majority.</p><a class="btn" href="#">READ MORE</a></div>
      <div class="acard"><span class="ph" role="img" aria-label="Cyclist on a forest road" style="background:linear-gradient(180deg,#9cb9cf,#5f7a83 55%,#3d4a3a)"></span><h4>Lorem Ipsum is simply dumt ext of the printing</h4><p>There are many variations of pass ages of Lorem Ipsum available but the majority.</p><a class="btn" href="#">READ MORE</a></div>
      <div class="acard"><span class="ph" role="img" aria-label="Mountain biker in green meadows" style="background:linear-gradient(180deg,#7eaad6,#7c9a5c 60%,#4d6a2e)"></span><h4>Lorem Ipsum is simply dumt ext of the printing</h4><p>There are many variations of pass ages of Lorem Ipsum available but the majority.</p><a class="btn" href="#">READ MORE</a></div>
    </div>
  </div>
</section>

<section class="band promo">
  <div class="wrap">
    <div class="band-head"><h2>PROMOTION</h2><a class="btn-outline" href="#">VIEW ALL PROMOTIONS</a></div>
    <div class="row2">
      <div class="pcard"><h3>Uferweg 8</h3><div class="price">CHF 3'519</div><div class="old">CHF 4'692</div><span class="off">25% OFF</span><a class="btn-outline" href="#">SHOP NOW</a><span class="ph" role="img" aria-label="Orange city bike"></span></div>
      <div class="pcard"><h3>Faltgut F3</h3><div class="price">CHF 2'358</div><div class="old">CHF 2'620</div><span class="off">10% OFF</span><a class="btn-outline" href="#">SHOP NOW</a><span class="ph" role="img" aria-label="Red folding bike"></span></div>
    </div>
  </div>
</section>

<section class="similar">
  <div class="wrap">
    <div class="band-head"><h2>SIMILAR PRODUCTS</h2><div class="arrows"><span>‹</span><span>›</span></div></div>
    <div class="row4">
      <div class="lcard" style="border:1px solid var(--line)"><span class="ph" role="img" aria-label="Black e-bike"></span><h5>Alpenbogen 14</h5><div class="price">CHF 5'751</div><ul><li>Performance : bike without engine</li><li>Type : bike trailer</li><li>Circuit : no</li><li>Size : universal</li><li>Vehicle ID : 272956</li></ul><a class="btn" href="#">ADD TO CART</a></div>
      <div class="lcard" style="border:1px solid var(--line)"><span class="ph" role="img" aria-label="Dark touring e-bike"></span><h5>Fernweh GT touring</h5><div class="price">CHF 7'112</div><ul><li>Performance : bike without engine</li><li>Type : bike trailer</li><li>Circuit : no</li><li>Size : universal</li><li>Vehicle ID : 272956</li></ul><a class="btn" href="#">ADD TO CART</a></div>
      <div class="lcard" style="border:1px solid var(--line)"><span class="ph" role="img" aria-label="Black e-bike"></span><h5>Hangar GH 5</h5><div class="price">CHF 5'259.-</div><ul><li>Performance : bike without engine</li><li>Type : bike trailer</li><li>Circuit : no</li><li>Size : universal</li><li>Vehicle ID : 272956</li></ul><a class="btn" href="#">ADD TO CART</a></div>
      <div class="lcard" style="border:1px solid var(--line)"><span class="ph" role="img" aria-label="Black e-bike"></span><h5>Anhänger Duo</h5><div class="price">1'199.-</div><ul><li>Performance : bike without engine</li><li>Type : bike trailer</li><li>Circuit : no</li><li>Size : universal</li><li>Vehicle ID : 272956</li></ul><a class="btn" href="#">ADD TO CART</a></div>
    </div>
  </div>
</section>

<footer class="site-footer">
  <div class="wrap" style="height:220px">
    <div class="f-logo">RAD LINDHOF</div>
    <div class="fcol" style="left:240px"><h6>LANGUAGES</h6><div>ENGLISH</div><div>FRANÇAIS</div><div>DEUTSCH</div></div>
    <div class="fcol" style="left:410px"><h6>CONTACT US</h6>
      <div class="fline"><svg width="10" height="14" viewBox="0 0 10 14"><path d="M5 13.5S1 8 1 5a4 4 0 0 1 8 0c0 3-4 8.5-4 8.5Z" fill="#c7c9cc"/><circle cx="5" cy="5" r="1.5" fill="#2b2d30"/></svg><span>Lindhofstrasse 12<br>8004 Zürich</span></div>
      <div class="fline"><svg width="12" height="12" viewBox="0 0 12 12"><path d="M2.5 1h2l1 3-1.5 1a7 7 0 0 0 3 3l1-1.5 3 1v2a1 1 0 0 1-1 1A10 10 0 0 1 1.5 2a1 1 0 0 1 1-1Z" fill="#c7c9cc"/></svg><span>+41 (0) 44 000 12 34</span></div>
      <div class="fline"><svg width="12" height="10" viewBox="0 0 12 10"><rect x=".5" y=".5" width="11" height="9" fill="none" stroke="#c7c9cc"/><path d="M.5 .5 6 5.5 11.5 .5" fill="none" stroke="#c7c9cc"/></svg><span>info@rad-lindhof.ch</span></div>
    </div>
    <div class="fcol" style="left:620px"><h6>MENU</h6><div>HOME</div><div>VELOS</div><div>NEWS</div><div>SERVICES</div><div>ABOUT US</div><div>FAQ</div><div>CONTACT US</div></div>
    <div class="fcol" style="left:790px"><h6>CONNECT WITH US</h6>
      <div class="social"><b></b>Friendwall</div>
      <div class="social"><b></b>Chirper</div>
      <div class="social"><b></b>WorkLink</div>
    </div>
  </div>
</footer>
<div class="copy">Copyright © 2019 All Rights Reserved</div>

</body>
</html>
```